BorrowNest Website design, we are a home loan / lending company

We are a finance broking company that can do mortgages / home loans, Car Loans, Commercial Loans, SMSF Loans, Business Loans, Personal Loans
We are looking for a simple website, not too busy, easy to navigate, something that prompts customers to action or call us.
I like the simplicity of the following websites:
https://www.velkarafinance.com.au/ - I like this website front page. I was thinking I have my logo, the one with the black background appear , then the toolbar at the top perhaps?
https://trevix.com.au/business-loans# - on this page there are images under finance that works for you that I like that concept.
https://dunmerel.com.au/contact/ - I like the Make an Appointment page
https://trevix.com.au/about-us - Simple but effective page design

Target Market(s)

Home Loan Customer

Industry/Entity Type

Finance / Home Loans

Coding

Coded - Design and coding required

Number of Pages Required

5+ page

Font styles to use
Serif

Colors
0094D4
00A9DD
6FCCEA
C7EBF8
E9F6FB

Requirements
Must have
• The following Heading s - Contact Us, About Us, Our People, Make an Appointment, Loan Options, Calculators, Reviews. I want to use the Logo colours I have in the zip files I uploaded.
Nice to have
• Simple clean design

```html
<!DOCTYPE html>
<html lang="en">
<head>
<meta charset="utf-8">
<title>BorrowNest – Home</title>
<link href="https://fonts.googleapis.com/css2?family=Montserrat:wght@500;600;700&family=Roboto:wght@400;500;700&display=swap" rel="stylesheet">
<style>
:root{
  --blue:#0094d4;
  --cyan:#00a9dd;
  --sky:#6fccea;
  --ice:#c7ebf8;
  --mist:#e9f6fb;
  --bright:#12d8f0;
  --ink:#222;
  --text:#444;
  --muted:#888;
  --footer:#3b3b3b;
  --white:#fff;
}
*{box-sizing:border-box;margin:0;padding:0}
html,body{width:1200px;height:3305px;overflow:hidden;background:var(--white)}
body{font-family:'Roboto',sans-serif;color:var(--text);position:relative}
.abs{position:absolute}
a{color:inherit;text-decoration:none}

/* header */
.header{position:absolute;left:0;top:0;width:1200px;height:113px;background:var(--white)}
.brand{position:absolute;left:110px;top:34px;font-family:'Montserrat',sans-serif;font-weight:700;font-size:36px;color:var(--ink);letter-spacing:-.5px}
.brand-dot{display:inline-block;width:12px;height:12px;border-radius:50%;background:var(--cyan);margin-left:4px;vertical-align:middle}
.phone-btn{position:absolute;left:665px;top:14px;width:44px;height:44px;border-radius:50%;background:var(--white);box-shadow:0 3px 12px rgba(0,0,0,.12);display:flex;align-items:center;justify-content:center}
.phone-num{position:absolute;left:726px;top:25px;font-size:15px;color:#555}
.appt{position:absolute;left:881px;top:13px;width:207px;height:46px;border:2.5px solid var(--cyan);border-radius:24px;font-size:13px;font-weight:700;color:var(--ink);display:flex;align-items:center;justify-content:center}
.nav{position:absolute;left:430px;top:81px;display:flex;gap:24px;font-size:13.5px;font-weight:500;color:var(--ink)}
.nav .active{color:var(--cyan)}

/* hero */
.hero{position:absolute;left:0;top:113px;width:1200px;height:600px;background:linear-gradient(100deg,#6b5a4c 0%,#a59683 30%,#b7b1a6 55%,#7d8a8c 80%,#4d5a60 100%)}
.hero-shade{position:absolute;inset:0;background:rgba(0,0,0,.25)}
.hero-copy{position:absolute;left:0;width:1200px;top:190px;text-align:center;color:var(--white)}
.hero-copy .kicker{font-family:'Montserrat',sans-serif;font-weight:700;font-size:20px}
.hero-copy h1{font-family:'Montserrat',sans-serif;font-weight:700;font-size:38px;margin-top:4px;letter-spacing:.5px}
.hero-copy .rule{width:70px;height:3px;background:var(--white);margin:6px auto 0}
.hero-copy p{font-size:16px;font-weight:500;line-height:26px;margin-top:18px}
.btn-grad{display:inline-flex;align-items:center;justify-content:center;border-radius:26px;background:linear-gradient(90deg,var(--bright),var(--blue));color:var(--white);font-weight:700;font-size:14px}
.hero-copy .btn-grad{width:154px;height:48px;margin-top:22px}
.arrow-circle{position:absolute;width:34px;height:34px;border-radius:50%;background:var(--white);display:flex;align-items:center;justify-content:center}
.hero-badge{position:absolute;left:548px;top:660px;width:104px;height:104px;border-radius:50%;background:var(--white);box-shadow:0 -2px 0 2px rgba(255,255,255,.6)}
.hero-badge::after{content:"";position:absolute;left:26px;top:26px;width:52px;height:52px;border-radius:50%;box-shadow:0 4px 14px rgba(0,0,0,.15)}
.hero-badge span{position:absolute;left:40px;top:40px;width:24px;height:24px;border-radius:50%;background:var(--cyan)}

/* bubbles */
.bubble{position:absolute;border-radius:50%;background:var(--mist)}

/* section titles */
.ghost{position:absolute;width:1200px;text-align:center;font-family:'Montserrat',sans-serif;font-weight:700;font-size:100px;color:#f1f1f1;letter-spacing:2px}
.title{position:absolute;width:1200px;text-align:center;font-family:'Montserrat',sans-serif;font-weight:700;font-size:35px;color:var(--ink)}
.title .light{font-weight:500;color:#555}
.title-rule{position:absolute;height:4px;width:92px;background:var(--cyan);border-radius:2px}

/* loan cards */
.card{position:absolute;width:308px;height:266px;background:var(--white);box-shadow:0 4px 18px rgba(0,0,0,.08);padding:0 19px}
.card .icon{position:absolute;left:19px;top:18px;width:78px;height:78px;border-radius:50%;background:linear-gradient(135deg,var(--bright),var(--blue));display:flex;align-items:center;justify-content:center}
.card h3{position:absolute;left:19px;top:115px;font-size:17.5px;font-weight:500;color:var(--ink)}
.card p{position:absolute;left:19px;right:19px;top:148px;font-size:14.5px;line-height:24px;color:#777;text-align:justify}
.card .go{position:absolute;left:19px;top:229px}
.card.featured{background:linear-gradient(160deg,var(--bright),var(--cyan) 55%,var(--blue))}
.card.featured .icon{background:var(--white)}
.card.featured h3,.card.featured p{color:var(--white)}

/* about */
.about-ghost{position:absolute;left:128px;top:1630px;font-family:'Montserrat',sans-serif;font-weight:700;font-size:100px;color:#f1f1f1}
.about-title{position:absolute;left:111px;top:1660px;font-family:'Montserrat',sans-serif;font-weight:700;font-size:35px;color:var(--ink)}
.about-title .light{font-weight:500;color:#555}
.about-copy{position:absolute;left:111px;top:1748px;width:470px;font-size:14.5px;line-height:26.5px;color:#888;text-align:justify}
.about-copy p+p{margin-top:11px}
.btn-line{position:absolute;display:flex;align-items:center;justify-content:center;border:2.5px solid var(--cyan);border-radius:26px;font-weight:500;font-size:14.5px;color:var(--ink)}
.about-photo{position:absolute;left:638px;top:1600px;width:600px;height:472px;border-radius:236px 0 0 236px;background:linear-gradient(120deg,#3e5774 0%,#8a9bad 40%,#d9c8bc 70%,#a4978a 100%)}

/* testimonials */
.review{position:absolute;top:2277px;width:308px;height:229px;background:var(--white);box-shadow:0 4px 18px rgba(0,0,0,.07);padding:0 26px}
.avatar{position:absolute;left:25px;top:31px;width:64px;height:64px;border-radius:50%;background:linear-gradient(160deg,#cfd8de,#7d8a95)}
.stars{position:absolute;left:115px;top:40px;color:#f3b400;font-size:10px;letter-spacing:1px}
.review h4{position:absolute;left:115px;top:54px;font-size:19px;font-weight:500;color:var(--ink)}
.review .date{position:absolute;left:115px;top:82px;font-size:10px;color:#999}
.review p{position:absolute;left:25px;right:25px;top:115px;font-size:14px;line-height:22.5px;color:#888;text-align:justify}

/* contact */
.contact{position:absolute;left:0;top:2598px;width:1200px;height:430px;background:linear-gradient(100deg,var(--cyan) 0%,var(--bright) 55%,var(--cyan) 100%)}
.contact-ring{position:absolute;left:-5px;top:2598px;width:430px;height:430px;border-radius:50%;background:var(--blue);border:0}
.contact-photo{position:absolute;left:20px;top:2620px;width:388px;height:388px;border-radius:50%;background:linear-gradient(150deg,#d9d4cb,#8c96a3 50%,#4e6a8f);border:6px solid var(--white)}
.contact-ghost{position:absolute;left:520px;top:2630px;font-family:'Montserrat',sans-serif;font-weight:700;font-size:76px;color:rgba(255,255,255,.18)}
.contact-title{position:absolute;left:520px;top:2648px;font-family:'Montserrat',sans-serif;font-weight:700;font-size:35px;color:var(--white)}
.contact-rule{position:absolute;left:520px;top:2702px;width:76px;height:4px;background:var(--white)}
.field{position:absolute;height:46px;background:var(--white);border:1px solid #ccc;font-size:14px;color:#666;padding:14px 15px}
.submit{position:absolute;left:712px;top:2936px;width:154px;height:50px;border-radius:26px;background:#2f2f2f;color:var(--white);font-weight:700;font-size:15px;display:flex;align-items:center;justify-content:center}

/* footer */
.footer{position:absolute;left:0;top:3028px;width:1200px;height:277px;background:var(--footer);color:#eee}
.footer .brand{left:110px;top:50px;color:var(--white)}
.copy{position:absolute;left:111px;top:115px;font-size:14px;line-height:26px}
.fcol{position:absolute;top:48px}
.fcol h5{font-size:16px;font-weight:500;color:#ccc;margin-bottom:18px}
.fcol a{display:block;font-size:14px;line-height:29px}
.social{display:flex;gap:9px}
.social span{width:34px;height:34px;border-radius:50%;background:#555}
.signup{position:absolute;left:780px;top:3222px;width:308px;height:42px;background:var(--white);border-radius:22px;font-size:13px;color:#666;padding:13px 18px}
.signup b{position:absolute;right:0;top:0;width:97px;height:42px;border-radius:22px;background:linear-gradient(90deg,var(--cyan),var(--blue));color:var(--white);font-size:14px;display:flex;align-items:center;justify-content:center}
.to-top{position:absolute;left:1064px;top:3010px;width:26px;height:26px;border-radius:50%;background:var(--white);display:flex;align-items:center;justify-content:center}
</style>
</head>
<body>

<header class="header">
  <div class="brand">BorrowNest<span class="brand-dot"></span></div>
  <div class="phone-btn"><svg width="18" height="18" viewBox="0 0 24 24"><path fill="#00a9dd" d="M6.6 10.8a15.2 15.2 0 0 0 6.6 6.6l2.2-2.2a1 1 0 0 1 1-.25 11.4 11.4 0 0 0 3.6.57 1 1 0 0 1 1 1V20a1 1 0 0 1-1 1A17 17 0 0 1 3 4a1 1 0 0 1 1-1h3.5a1 1 0 0 1 1 1c0 1.25.2 2.45.57 3.57a1 1 0 0 1-.25 1z"/></svg></div>
  <div class="phone-num">+1 (555) 014 2290</div>
  <a class="appt" href="#">MAKE AN APPOINTMENT</a>
  <nav class="nav">
    <a class="active" href="#">HOME</a><a href="#">ABOUT US</a><a href="#">OUR PEOPLE</a><a href="#">LOAN OPTIONS</a><a href="#">CALCULATORS</a><a href="#">REVIEWS</a><a href="#">CONTACT US</a>
  </nav>
</header>

<section class="hero" role="img" aria-label="Photo of a smiling loan broker in glasses talking with a client across an office desk with a laptop">
  <div class="hero-shade"></div>
  <div class="hero-copy">
    <div class="kicker">WELCOME TO</div>
    <h1>BORROWNEST</h1>
    <div class="rule"></div>
    <p>Lorem ipsum dolor sit amet, consectetur adipiscing elit<br>sed do eiusmod tempor incidiea.</p>
    <a class="btn-grad" href="#">GET STARTED</a>
  </div>
  <div class="arrow-circle" style="left:38px;top:283px"><svg width="12" height="12" viewBox="0 0 12 12"><path d="M8 1 3 6l5 5" stroke="#222" stroke-width="2" fill="none"/></svg></div>
  <div class="arrow-circle" style="left:1127px;top:283px"><svg width="12" height="12" viewBox="0 0 12 12"><path d="m4 1 5 5-5 5" stroke="#222" stroke-width="2" fill="none"/></svg></div>
</section>
<div class="hero-badge"><span></span></div>

<div class="bubble" style="left:1128px;top:740px;width:130px;height:130px"></div>
<div class="bubble" style="left:1096px;top:865px;width:56px;height:56px"></div>
<div class="bubble" style="left:-70px;top:1435px;width:138px;height:138px"></div>
<div class="bubble" style="left:45px;top:1563px;width:57px;height:57px"></div>
<div class="bubble" style="left:-70px;top:2108px;width:138px;height:138px"></div>
<div class="bubble" style="left:45px;top:2068px;width:57px;height:57px"></div>

<div class="ghost" style="top:790px">SERVICES</div>
<h2 class="title" style="top:825px"><span class="light">LOAN</span> OPTIONS</h2>
<div class="title-rule" style="left:553px;top:872px"></div>

<article class="card" style="left:112px;top:926px">
  <div class="icon"><svg width="40" height="40" viewBox="0 0 40 40" fill="none" stroke="#fff" stroke-width="2"><path d="M6 19 20 7l14 12M10 16v17h20V16"/><circle cx="20" cy="24" r="5"/></svg></div>
  <h3>MORTGAGES LOANS</h3>
  <p>Sed ut perspiciatis unde omnis iste natus error sit voluptatem accusantium dolore amque laudantium totea.</p>
  <svg class="go" width="28" height="14" viewBox="0 0 28 14" fill="none" stroke="#222" stroke-width="2"><path d="M0 7h26M20 1l6 6-6 6"/></svg>
</article>
<article class="card" style="left:446px;top:926px">
  <div class="icon"><svg width="40" height="40" viewBox="0 0 40 40" fill="none" stroke="#fff" stroke-width="2"><path d="M6 26v-6l4-8h20l4 8v6z"/><circle cx="12" cy="28" r="3"/><circle cx="28" cy="28" r="3"/></svg></div>
  <h3>CAR LOANS</h3>
  <p>Sed ut perspiciatis unde omnis iste natus error sit voluptatem accusantium dolore amque laudantium totea.</p>
  <svg class="go" width="28" height="14" viewBox="0 0 28 14" fill="none" stroke="#222" stroke-width="2"><path d="M0 7h26M20 1l6 6-6 6"/></svg>
</article>
<article class="card featured" style="left:780px;top:926px">
  <div class="icon"><svg width="40" height="40" viewBox="0 0 40 40" fill="none" stroke="#0094d4" stroke-width="2"><ellipse cx="22" cy="10" rx="7" ry="3"/><path d="M15 10v12c0 2 14 2 14 0V10M6 30h10l8-3 8 3"/></svg></div>
  <h3>COMMERCIAL LOANS</h3>
  <p>Sed ut perspiciatis unde omnis iste natus error sit voluptatem accusantium dolore amque laudantium totea.</p>
  <svg class="go" width="28" height="14" viewBox="0 0 28 14" fill="none" stroke="#fff" stroke-width="2"><path d="M0 7h26M20 1l6 6-6 6"/></svg>
</article>
<article class="card" style="left:112px;top:1215px">
  <div class="icon"><svg width="40" height="40" viewBox="0 0 40 40" fill="none" stroke="#fff" stroke-width="2"><rect x="11" y="8" width="20" height="18" rx="2"/><circle cx="21" cy="17" r="5"/><path d="M5 30h10l8-3 10 3"/></svg></div>
  <h3>SMSF LOANS</h3>
  <p>Sed ut perspiciatis unde omnis iste natus error sit voluptatem accusantium dolore amque laudantium totea.</p>
  <svg class="go" width="28" height="14" viewBox="0 0 28 14" fill="none" stroke="#222" stroke-width="2"><path d="M0 7h26M20 1l6 6-6 6"/></svg>
</article>
<article class="card" style="left:446px;top:1215px">
  <div class="icon"><svg width="40" height="40" viewBox="0 0 40 40" fill="none" stroke="#fff" stroke-width="2"><circle cx="20" cy="14" r="7"/><path d="M6 28l8-4h12l8 4M10 32h20"/></svg></div>
  <h3>BUSINESS LOANS</h3>
  <p>Sed ut perspiciatis unde omnis iste natus error sit voluptatem accusantium dolore amque laudantium totea.</p>
  <svg class="go" width="28" height="14" viewBox="0 0 28 14" fill="none" stroke="#222" stroke-width="2"><path d="M0 7h26M20 1l6 6-6 6"/></svg>
</article>
<article class="card" style="left:780px;top:1215px">
  <div class="icon"><svg width="40" height="40" viewBox="0 0 40 40" fill="none" stroke="#fff" stroke-width="2"><circle cx="17" cy="13" r="5"/><path d="M7 32c0-7 4-11 10-11s10 4 10 11"/><circle cx="29" cy="24" r="4"/></svg></div>
  <h3>PERSONAL LOANS</h3>
  <p>Sed ut perspiciatis unde omnis iste natus error sit voluptatem accusantium dolore amque laudantium totea.</p>
  <svg class="go" width="28" height="14" viewBox="0 0 28 14" fill="none" stroke="#222" stroke-width="2"><path d="M0 7h26M20 1l6 6-6 6"/></svg>
</article>

<div class="about-ghost">ABOUT</div>
<h2 class="about-title">ABOUT <span class="light">US</span></h2>
<div class="title-rule" style="left:111px;top:1709px;width:76px"></div>
<div class="about-copy">
  <p>Sed ut perspiciatis unde omnis iste natus error sit voluptatem accus antium doloremque laudantium, totam rem aperiam, eaque ipsa quae ab illo inven tore veritatis et quasi architecto beatae vitae dicta sunt explic abo nemo enim ipsam voluptatem quia voluptasea.</p>
  <p>Sit aspernatur aut odit aut fugit, sed quia consequuntur magni dolores eos qui ratione voluptatem sequi nesciunt. Neque porro quisquam est, qui dolorem ipsum quia dolor sit ametra.</p>
</div>
<a class="btn-line" href="#" style="left:111px;top:1977px;width:146px;height:50px">READ MORE</a>
<div class="about-photo" role="img" aria-label="Photo of a broker and two clients reviewing paperwork at a table beside a small wooden house model"></div>

<div class="ghost" style="top:2137px">REVIEWS</div>
<h2 class="title" style="top:2172px">TESTIMONIALS</h2>
<div class="title-rule" style="left:553px;top:2219px"></div>

<svg class="abs" style="left:48px;top:2383px" width="26" height="16" viewBox="0 0 26 16" fill="none" stroke="#999" stroke-width="2"><path d="M26 8H2M8 1 1 8l7 7"/></svg>
<svg class="abs" style="left:1127px;top:2383px" width="26" height="16" viewBox="0 0 26 16" fill="none" stroke="#444" stroke-width="2"><path d="M0 8h24M18 1l7 7-7 7"/></svg>

<article class="review" style="left:112px">
  <div class="avatar" role="img" aria-label="Reviewer portrait"></div>
  <div class="stars">★★★★★</div><h4>Marcus Reed</h4><div class="date">June 2022</div>
  <p>Lorem ipsum dolor sit amet, consectetur adipiscing elit, sed do eiusmod tempor incididunt ut labore et dolore magna aliq ua enim ad minim veniamea.</p>
</article>
<article class="review" style="left:446px">
  <div class="avatar" role="img" aria-label="Reviewer portrait"></div>
  <div class="stars">★★★★★</div><h4>Marcus Reed</h4><div class="date">June 2022</div>
  <p>Lorem ipsum dolor sit amet, consectetur adipiscing elit, sed do eiusmod tempor incididunt ut labore et dolore magna aliq ua enim ad minim veniamea.</p>
</article>
<article class="review" style="left:780px">
  <div class="avatar" role="img" aria-label="Reviewer portrait"></div>
  <div class="stars">★★★★★</div><h4>Marcus Reed</h4><div class="date">June 2022</div>
  <p>Lorem ipsum dolor sit amet, consectetur adipiscing elit, sed do eiusmod tempor incididunt ut labore et dolore magna aliq ua enim ad minim veniamea.</p>
</article>

<section class="contact" role="img" aria-label="Bright cyan background band"></section>
<div class="contact-ring"></div>
<div class="contact-photo" role="img" aria-label="Photo of a smiling man in glasses reading a letter"></div>
<div class="contact-ghost">CONTACT</div>
<h2 class="contact-title">CONTACT US</h2>
<div class="contact-rule"></div>
<div class="field" style="left:521px;top:2735px;width:262px">First Name</div>
<div class="field" style="left:793px;top:2735px;width:263px">Last Name</div>
<div class="field" style="left:521px;top:2791px;width:262px">Phone</div>
<div class="field" style="left:793px;top:2791px;width:263px">Email</div>
<div class="field" style="left:521px;top:2847px;width:535px;height:78px">Message</div>
<a class="submit" href="#">SUBMIT</a>

<footer class="footer">
  <div class="brand">BorrowNest<span class="brand-dot"></span></div>
  <div class="copy">Copyrights © 2022 BorrowNest<br>All Rights Reserved</div>
  <div class="fcol" style="left:449px"><h5>OVERVIEW</h5><a href="#">Home</a><a href="#">About Us</a><a href="#">Our People</a><a href="#">Loan Options</a><a href="#">Calculators</a><a href="#">Contact Us</a></div>
  <div class="fcol" style="left:618px"><h5>LIBRARY</h5><a href="#">Privacy Policy</a><a href="#">Terms Of Use</a><a href="#">Disclaimer</a><a href="#">Reviews</a></div>
  <div class="fcol" style="left:778px"><h5>FOLLOW US</h5><div class="social"><span></span><span></span><span></span></div><h5 style="margin-top:34px">SIGN UP FOR UPDATES</h5></div>
</footer>
<div class="signup">Email Address<b>SIGN UP</b></div>
<div class="to-top"><svg width="10" height="16" viewBox="0 0 10 16" fill="none" stroke="#222" stroke-width="1.6"><path d="M5 16V1M1 5l4-4 4 4"/></svg></div>

</body>
</html>
```